Brivolt Technologies business card design

We need a business card designed with our new logo. it would be great if the card could communicate it is a technology based company.

Target Market(s)

system integrators

Industry/Entity Type

technology, IOT

Contact Information for Business Card

Name, designation, Address, telephone number, email address

Requirements
Must have
• logo and company name
Nice to have
• something to do with technology

```html
<!DOCTYPE html>
<html lang="en">
<head>
<meta charset="utf-8">
<title>Brivolt Technologies – Business Card</title>
<link href="https://fonts.googleapis.com/css2?family=Arimo:wght@400;700&display=swap" rel="stylesheet">
<style>
  :root {
    --bg: #999999;
    --card-light: #ffffff;
    --card-dark: #383838;
    --accent: #f39021;
    --ink: #333333;
    --ink-soft: #222222;
  }
  * { margin: 0; padding: 0; box-sizing: border-box; }
  html, body {
    width: 1200px; height: 1059px; overflow: hidden;
    background: var(--bg);
    font-family: "Arimo", Arial, sans-serif;
  }
  .canvas { position: relative; width: 1200px; height: 1059px; }
  .card {
    position: absolute; left: 256px; width: 688px; height: 391px;
    border-radius: 22px;
  }
  .card--front { top: 89px; background: var(--card-light); }
  .card--back { top: 569px; background: var(--card-dark); }

  .brand {
    position: absolute; left: 0; right: 0;
    display: flex; align-items: center; justify-content: center; gap: 14px;
  }
  .brand__mark { width: 24px; height: 24px; background: var(--accent); }
  .brand__name {
    font-weight: 700; font-size: 32px; letter-spacing: 1px;
    text-transform: uppercase;
  }
  .card--front .brand { top: 82px; }
  .card--front .brand__name { color: var(--ink); }
  .card--back .brand { top: 172px; }
  .card--back .brand__name { color: var(--accent); font-size: 36px; }

  .person { position: absolute; top: 193px; left: 0; right: 0; text-align: center; }
  .person__name { color: var(--accent); font-weight: 700; font-size: 26px; line-height: 30px; }
  .person__role { color: var(--ink-soft); font-size: 17px; line-height: 24px; }

  .address {
    position: absolute; right: 370px; top: 288px;
    text-align: right; color: var(--ink-soft); font-size: 17px; line-height: 21px;
  }
  .divider {
    position: absolute; left: 344px; top: 279px; width: 1px; height: 65px;
    background: var(--ink);
  }
  .contacts { position: absolute; left: 369px; top: 272px; list-style: none; }
  .contacts li {
    display: flex; align-items: center; gap: 6px;
    height: 27px; color: var(--ink-soft); font-size: 17px;
  }
  .contacts svg { width: 13px; height: 13px; flex: none; }
</style>
</head>
<body>
<main class="canvas">
  <section class="card card--front">
    <div class="brand">
      <span class="brand__mark"></span>
      <span class="brand__name">Brivolt Technologies</span>
    </div>
    <div class="person">
      <p class="person__name">DANIEL HARTWELL</p>
      <p class="person__role">CEO/Founder</p>
    </div>
    <address class="address" style="font-style:normal">
      2180 Harbor Lane<br>Northvale CD 4172
    </address>
    <div class="divider"></div>
    <ul class="contacts">
      <li>
        <svg viewBox="0 0 16 16"><path fill="#f39021" d="M3 1.5l3 3-1.6 1.8a9 9 0 0 0 5.3 5.3L11.5 10l3 3-2 2C6.5 15 1 9.5 1 3.5z"/></svg>
        (123) 555-0148
      </li>
      <li>
        <svg viewBox="0 0 16 16"><rect x="1" y="3" width="14" height="10" fill="#f39021"/><path d="M1 3l7 6 7-6" fill="none" stroke="#fff" stroke-width="1.3"/></svg>
        info@brivolttech.com
      </li>
      <li>
        <svg viewBox="0 0 16 16" fill="none" stroke="#f39021" stroke-width="1.2"><circle cx="8" cy="8" r="6.5"/><ellipse cx="8" cy="8" rx="3" ry="6.5"/><path d="M1.5 8h13M2.5 4.5h11M2.5 11.5h11"/></svg>
        www.brivolttech.com
      </li>
    </ul>
  </section>

  <section class="card card--back">
    <div class="brand">
      <span class="brand__mark"></span>
      <span class="brand__name">Brivolt Technologies</span>
    </div>
  </section>
</main>
</body>
</html>
```